Elegant, Playful ReDesign of Paperlynx Website in wordpress - Budget has been raised

Project Brief: Paperlynx Website Redesign in WordPress

Introduction: Paperlynx, a cutting-edge document creation solution, aims to revolutionize the tedious process of crafting contracts, offers, forms, and other documents. By saving customers valuable time, streamlining workflows, and minimizing human error, Paperlynx has become an essential tool. As a technology company with a diverse clientele, we're set to boost our online presence through a refreshed WordPress website. Beyond a modernized website, we aspire to establish a stronger brand identity, incorporating graphic elements seamlessly into our online presence.

Current Status: Currently hosted on WordPress, Paperlynx's existing website serves its purpose but is ready for a visual transformation. Our goal is to maintain a modern and attractive appearance while upholding our commitment to simplicity and efficiency. Notably, the website is currently only in Danish. The redesigned structure should include a language switch function to cater to future international customers.

Objectives:
• Modern Aesthetic: Redesign the website with a fresh and modern vibe, reflecting innovation in the document creation sphere.
• User-Friendly: Prioritize an intuitive design for seamless navigation, ensuring visitors easily understand our offerings and benefits.
• Informative Content: Strike a balance between attractiveness and informativeness, clearly communicating Paperlynx's value proposition and simplifying business processes.
• Graphic Elements: Integrate visually appealing graphics that enhance the site's aesthetics and contribute to our overall visual identity. These elements should be versatile for future use in social media, advertisements, and other branding materials.
• Brand Recognition: Maintain our current logo and color scheme while exploring creative ways to establish a distinctive brand identity. The website should be a cornerstone for a cohesive branding strategy.
• Media Integration: Include images or videos on the website to enhance engagement. Find suitable, free-to-use visuals.
• Responsiveness: Ensure the design is responsive and works seamlessly on all devices.
• Demo Booking Form: Improve the design of the form to book a demo.
• Multilingual Support: Enable language transformation; the website is currently in Danish but should cater to other countries.

Guidelines:
• Typography: Up to the designer's discretion.
• Images/Videos: Must be free to use without additional charges.
• WordPress Theme: Use any WordPress theme below $100.
• Logo Redesign: Not needed; stick to the referenced color palette, as our new logo uses these colors.
• Color Palette: Stick to the existing company colors for consistency:
RGB
• #000b3c
• #004c6c
• #319ac3
• Greytones and white are also allowed
• Creativity Encouraged: Embrace creativity within the color palette for the layout, visuals, and overall user experience.

Conclusion: The Paperlynx website redesign marks an exciting opportunity to enhance our online presence. Our goal is to achieve a balance between a modern, attractive design and a clear, informative representation of our innovative solutions. We envision the revamped website as the foundation for a compelling online brand presence, with versatile graphic elements resonating across various digital platforms.

Sections that the website must include: Space for customer logos, space for testimonials, Space and redesign for display of price structure and price comparison, sections for company details and other information.

Design should also include a redesign of the customer cases section.
Generally there should just be a redesign of all things that are on the website.

Link to current website: https://paperlynx.example/

Target Market(s)

+50 employees.

Industry/Entity Type

Document automation

Coding

Coded - Design and coding required

Number of Pages Required

5+ page

Colors
0054AA
0677BA
7BADD7
CADEEF
E8F1F8

Requirements
Must have
• The new webpage must have the same pages as the current one. Frontpage, Book demo, About us, Case stories and Pricing

```html
<!DOCTYPE html>
<html lang="en">
<head>
<meta charset="utf-8">
<title>Paperlynx – Create error free contracts and quotes quickly</title>
<link rel="stylesheet" href="https://fonts.googleapis.com/css2?family=Barlow+Semi+Condensed:wght@600;700&family=Roboto:wght@400;500;700&display=swap">
<style>
:root{
  --navy:#000b3c;
  --deep:#004c6c;
  --blue:#1c9ad6;
  --blue-2:#319ac3;
  --ink:#111;
  --text:#555;
  --muted:#888;
  --grey-bg:#f5f5f5;
  --line:#e6e6e6;
  --white:#fff;
  --black:#000;
}
*{box-sizing:border-box;margin:0;padding:0}
html,body{width:1200px;height:5008px;overflow:hidden;background:var(--white)}
body{font-family:"Roboto",sans-serif;color:var(--text);position:relative}
.heading{font-family:"Barlow Semi Condensed",sans-serif;font-weight:700;color:var(--ink);text-transform:uppercase;text-align:center}
.abs{position:absolute}

/* header */
.site-header{position:absolute;top:0;left:0;width:1200px;height:103px;background:var(--white)}
.brand{position:absolute;left:111px;top:34px;display:flex;align-items:center;gap:10px}
.brand-mark{width:30px;height:30px;background:var(--deep)}
.brand-name{font-family:"Barlow Semi Condensed",sans-serif;font-weight:700;font-size:28px;color:var(--deep);letter-spacing:.5px}
.main-nav{position:absolute;left:368px;top:38px;display:flex;gap:22px;font-size:13px;color:var(--ink)}
.lang{position:absolute;left:925px;top:26px;display:flex;align-items:center;gap:14px;font-size:15px;font-weight:700;color:var(--ink)}
.lang-dot{width:38px;height:38px;border-radius:50%;background:#2a3f8f;border:4px solid #d8dce8}

/* hero */
.hero{position:absolute;top:103px;left:0;width:1200px;height:572px}
.hero-photo{position:absolute;inset:0;background:linear-gradient(90deg,#cfd6dc 0%,#e6e8e9 35%,#b9a89a 60%,#6f6a66 80%,#3f4650 100%)}
.hero-panel{position:absolute;left:0;top:0}
.hero-copy{position:absolute;left:111px;top:136px;color:var(--white)}
.hero-brand{display:flex;align-items:center;gap:10px;margin-bottom:22px}
.hero-brand .brand-mark{width:28px;height:28px;background:var(--white)}
.hero-brand span{font-family:"Barlow Semi Condensed",sans-serif;font-weight:700;font-size:24px}
.hero-title{font-family:"Barlow Semi Condensed",sans-serif;font-weight:700;font-size:52px;line-height:54px;text-transform:uppercase}
.btn-dark{display:inline-block;margin-top:22px;background:var(--navy);color:var(--white);font-size:13px;font-weight:700;padding:16px 34px;border-radius:30px;text-transform:uppercase}

/* logos */
.clients{position:absolute;left:111px;top:729px;width:978px;height:179px;background:#f7f7f7}
.client{position:absolute;display:flex;align-items:center;gap:8px;font-family:"Roboto",sans-serif;font-weight:700;color:#8a8a8a}
.client i{display:block;width:16px;height:16px;background:#b5b5b5}

/* pricing */
.price-card{position:absolute;top:1050px;width:288px;background:var(--white);box-shadow:0 10px 40px rgba(0,0,0,.09);text-align:center;padding-top:30px}
.plan{font-family:"Barlow Semi Condensed",sans-serif;font-weight:600;font-size:24px;color:var(--blue);text-transform:uppercase}
.amount{font-family:"Barlow Semi Condensed",sans-serif;font-weight:700;font-size:44px;color:var(--ink);line-height:52px}
.per{font-size:15px;font-weight:500;color:var(--deep);margin-top:8px}
.docs{font-size:11px;color:var(--muted);margin-top:10px;text-transform:uppercase}
.features{list-style:none;margin-top:26px;font-size:13.5px;color:#555}
.features li{height:31.7px}
.save{position:absolute;right:14px;top:6px;width:66px;height:66px;border-radius:50%;background:var(--blue);border:4px solid #cde6f3;color:var(--white);font-family:"Barlow Semi Condensed",sans-serif;font-weight:700;line-height:1;display:flex;flex-direction:column;justify-content:center}
.save small{font-size:10px}
.save b{font-size:18px}
.btn-blue{display:inline-flex;align-items:center;gap:8px;background:var(--blue);color:var(--white);font-size:13px;font-weight:500;padding:13px 28px;border-radius:30px;text-transform:uppercase}

/* videos */
.video-band{position:absolute;top:1882px;left:0;width:1200px;height:451px;background:var(--grey-bg)}
.tabs{position:absolute;top:2035px;left:0;width:1200px;display:flex;justify-content:center;gap:18px}
.tab{height:46px;border-radius:26px;padding:0 34px;display:flex;align-items:center;font-size:12.5px;font-weight:700;color:var(--ink);background:var(--white);box-shadow:0 4px 14px rgba(0,0,0,.1);text-transform:uppercase}
.tab.active{background:var(--blue);color:var(--white)}
.video{position:absolute;left:194px;top:2135px;width:800px;height:435px;background:var(--white);box-shadow:0 8px 30px rgba(0,0,0,.15);overflow:hidden}
.feat-col{position:absolute;top:2632px;list-style:none;font-size:15px;color:#333}
.feat-col li{height:34px;display:flex;align-items:center;gap:7px}

/* testimonials */
.reviews{position:absolute;top:3003px;left:0;width:1200px;height:691px;background:var(--grey-bg)}
.review-card{position:absolute;left:270px;top:3217px;width:661px;height:370px;background:var(--white);box-shadow:0 6px 30px rgba(0,0,0,.08);text-align:center}
.avatar{position:absolute;border-radius:50%;background:linear-gradient(135deg,#6b5a4e,#c9a994);border:3px solid var(--white)}
.quote{font-size:14.5px;line-height:25px;color:#777;margin:0 auto;width:560px}
.arrow{position:absolute;width:30px;height:30px;border-radius:50%;background:var(--deep);display:flex;align-items:center;justify-content:center}

/* demo form */
.field{position:absolute;background:var(--white);box-shadow:0 2px 12px rgba(0,0,0,.08);font-size:14.5px;color:#333;padding:0 20px;display:flex;align-items:center}

/* footer */
.site-footer{position:absolute;top:4452px;left:0;width:1200px;height:556px;background:var(--black);color:var(--white)}
.foot-h{font-family:"Barlow Semi Condensed",sans-serif;font-weight:600;font-size:21px;text-transform:uppercase;position:absolute;top:233px}
.foot-list{position:absolute;list-style:none;font-size:12.5px;line-height:30px}
</style>
</head>
<body>

<header class="site-header">
  <div class="brand"><span class="brand-mark"></span><span class="brand-name">PAPERLYNX</span></div>
  <nav class="main-nav">
    <span>Paperlynx</span><span>front page</span><span>Customer cases</span><span>Video</span><span>Live demo</span><span>Prices</span><span>More</span>
  </nav>
  <div class="lang"><span class="lang-dot"></span><span>En ▾</span></div>
  <svg class="abs" style="left:905px;top:0" width="120" height="103"><line x1="118" y1="0" x2="58" y2="103" stroke="#1c9ad6" stroke-width="2"/></svg>
</header>

<section class="hero">
  <div class="hero-photo" role="img" aria-label="Photo of two business people reviewing a contract at a desk"></div>
  <svg class="hero-panel" width="680" height="572" aria-hidden="true">
    <path d="M95 86 H636 L590 476 H70 V111 Q70 86 95 86 Z" fill="#1c9ad6"/>
    <path d="M636 86 L660 86 L612 476 L590 476 Z" fill="#ffffff" opacity=".85"/>
  </svg>
  <div class="hero-copy" style="top:140px">
    <div class="hero-brand"><span class="brand-mark"></span><span>PAPERLYNX</span></div>
    <h1 class="hero-title">Create error<br>free contracts<br>and quotes quickly</h1>
    <span class="btn-dark">Get started</span>
  </div>
</section>

<section class="clients" aria-label="Our customers">
  <div class="client" style="left:48px;top:42px;font-size:15px"><i></i>NORTHPEAK</div>
  <div class="client" style="left:262px;top:38px;font-size:17px"><i></i>LUMEN LEGAL</div>
  <div class="client" style="left:412px;top:36px;font-size:24px;font-weight:400"><i></i>Crateway</div>
  <div class="client" style="left:592px;top:34px;font-size:24px"><i></i>Webnook</div>
  <div class="client" style="left:756px;top:42px;font-size:13px"><i></i>QUILLDOCS</div>
  <div class="client" style="left:68px;top:112px;font-size:32px">Verano</div>
  <div class="client" style="left:243px;top:114px;font-size:26px">Brightly</div>
  <div class="client" style="left:410px;top:116px;font-size:19px;font-weight:400"><i></i>Deskline</div>
  <div class="client" style="left:623px;top:118px;font-size:13px"><i></i>CLEARLAW</div>
  <div class="client" style="left:770px;top:110px;font-size:28px;font-weight:500">holmberg</div>
</section>

<h2 class="heading abs" style="top:952px;left:0;width:1200px;font-size:36px">Our pricing</h2>

<article class="price-card" style="left:132px;height:461px">
  <div class="save"><small>SAVE DKK</small><b>295.</b></div>
  <div class="plan">Starter</div><div class="amount">950 kr.</div>
  <div class="per">PER MONTH</div><div class="docs">250 documents / year</div>
  <ul class="features"><li>1 contract template</li><li>1 user</li><li>+ DKK 95 per additional user</li><li>Export to Word</li><li>Export to Pdf</li><li>Own design</li></ul>
  <span class="btn-blue" style="margin-top:16px">● Book demo</span>
</article>

<article class="price-card" style="left:457px;height:681px">
  <div class="save"><small>SAVE DKK</small><b>295.</b></div>
  <div class="plan">Pro</div><div class="amount">1.595 kr.</div>
  <div class="per">PER MONTH</div><div class="docs">1.000 documents / year</div>
  <ul class="features"><li>2 contract templates</li><li>1 user</li><li>+ DKK 95 per additional user</li><li>Export to Word</li><li>Export to Pdf</li><li>Own design</li><li>Digital signature</li><li>Reviewproces</li><li>More languages</li><li>Product listing</li><li>Employee posting</li><li>Documents in mail</li><li>Integration to CRM</li></ul>
  <span class="btn-blue" style="margin-top:16px">● Book demo</span>
</article>

<article class="price-card" style="left:782px;height:750px">
  <div class="save"><small>SAVE DKK</small><b>295.</b></div>
  <div class="plan">Business</div><div class="amount">2.795 kr.</div>
  <div class="per">PER MONTH</div><div class="docs">2000 documents / year</div>
  <ul class="features"><li>4 contract templates</li><li>1 user</li><li>+ DKK 95 per additional user</li><li>Export to Word</li><li>Export to Pdf</li><li>Own design</li><li>Digital signature</li><li>Reviewproces</li><li>More languages</li><li>Product listing</li><li>Employee posting</li><li>Documents in mail</li><li>Integration to CRM</li><li>Customer/client request</li><li>Raw data in Excel</li><li>API access</li></ul>
  <span class="btn-blue" style="margin-top:16px">● Book demo</span>
</article>

<div class="video-band"></div>
<h2 class="heading abs" style="top:1948px;left:0;width:1200px;font-size:36px">Videos</h2>
<div class="tabs">
  <span class="tab active">Lots of features</span><span class="tab">Sign with Inkwell</span><span class="tab">Integration to CRM</span>
</div>
<div class="video">
  <div style="position:absolute;inset:0" role="img" aria-label="Video preview showing the document builder inside a CRM screen">
    <div style="height:14px;background:#2d4a63"></div>
    <div style="position:absolute;left:0;top:14px;width:70px;bottom:0;background:#eef1f4"></div>
    <div style="position:absolute;left:80px;top:30px;width:340px;height:250px;background:#f7f8f9;border:1px solid #e2e5e8"></div>
    <div style="position:absolute;left:450px;top:40px;width:340px;height:20px;background:#8fa3b4"></div>
    <div style="position:absolute;left:450px;top:75px;width:160px;height:50px;background:#e6ecf1"></div>
    <div style="position:absolute;left:620px;top:75px;width:160px;height:50px;background:#e6ecf1"></div>
    <div style="position:absolute;left:450px;top:140px;width:160px;height:50px;background:#e6ecf1"></div>
  </div>
  <svg class="abs" style="left:376px;top:196px" width="48" height="48"><circle cx="24" cy="24" r="24" fill="#004c6c"/><path d="M19 15 L34 24 L19 33 Z" fill="#fff"/></svg>
</div>

<ul class="feat-col" style="left:146px">
  <li><span style="color:var(--blue)">✔</span>Own design</li><li><span style="color:var(--blue)">✔</span>Calculation of values</li><li><span style="color:var(--blue)">✔</span>Sections are inserted automatically</li><li><span style="color:var(--blue)">✔</span>Process for review</li><li><span style="color:var(--blue)">✔</span>Digital signature</li>
</ul>
<ul class="feat-col" style="left:471px">
  <li><span style="color:var(--blue)">✔</span>Lookup in the CVR register</li><li><span style="color:var(--blue)">✔</span>Global address register</li><li><span style="color:var(--blue)">✔</span>Download som Word</li><li><span style="color:var(--blue)">✔</span>Download as Pdf</li><li><span style="color:var(--blue)">✔</span>Data i Excel</li>
</ul>
<ul class="feat-col" style="left:792px">
  <li><span style="color:var(--blue)">✔</span>Document designer</li><li><span style="color:var(--blue)">✔</span>Share with colleagues</li><li><span style="color:var(--blue)">✔</span>Integration to CRM</li><li><span style="color:var(--blue)">✔</span>Integration for case management</li><li><span style="color:var(--blue)">✔</span>More languages</li>
</ul>

<section class="reviews">
  <h2 class="heading" style="margin-top:90px;font-size:38px">Appreciated and recommended by</h2>
</section>
<div class="avatar" role="img" aria-label="Customer portrait" style="left:110px;top:3133px;width:50px;height:50px"></div>
<div class="avatar" role="img" aria-label="Customer portrait" style="left:1042px;top:3133px;width:50px;height:50px"></div>
<div class="avatar" role="img" aria-label="Customer portrait" style="left:211px;top:3252px;width:50px;height:50px"></div>
<div class="avatar" role="img" aria-label="Customer portrait" style="left:942px;top:3252px;width:50px;height:50px"></div>
<div class="review-card">
  <p class="quote" style="margin-top:98px">I didn't imagine our offer could be fully automated just like that, but we gave it a shot because I saw what others had done with Paperlynx.</p>
  <p class="quote" style="margin-top:25px">The result has become razor sharp – I am completely happy when I stand with a new offer in my hand.</p>
  <div style="width:565px;height:1px;background:var(--line);margin:30px auto 0"></div>
  <div style="position:relative;margin-top:26px">
    <span class="abs" style="left:100px;top:-20px;font-family:Georgia,serif;font-size:110px;color:#e3e3e3;line-height:1">“</span>
    <span class="abs" style="right:90px;top:-20px;font-family:Georgia,serif;font-size:110px;color:#e3e3e3;line-height:1">”</span>
    <div style="font-size:17px;font-weight:700;color:var(--ink)">Mikkel Aagaard Sørensen</div>
    <div style="font-size:14px;color:#444;margin-top:8px">Sales director – Fortgate Security</div>
  </div>
</div>
<div class="avatar" role="img" aria-label="Portrait of the quoted customer" style="left:555px;top:3172px;width:92px;height:92px"></div>
<div class="arrow" style="left:201px;top:3378px"><svg width="10" height="10"><path d="M7 1 L3 5 L7 9" stroke="#fff" stroke-width="2" fill="none"/></svg></div>
<div class="arrow" style="left:971px;top:3378px"><svg width="10" height="10"><path d="M3 1 L7 5 L3 9" stroke="#fff" stroke-width="2" fill="none"/></svg></div>

<svg class="abs" style="left:86px;top:3800px" width="50" height="76" aria-hidden="true"><circle cx="38" cy="38" r="34" fill="none" stroke="#1c9ad6" stroke-width="1.5" transform="translate(-12,0)"/></svg>
<h2 class="heading abs" style="top:3775px;left:0;width:1160px;font-size:40px">Book a demo</h2>
<p class="abs" style="top:3840px;left:235px;width:690px;text-align:center;font-size:14.5px;line-height:26px;color:#333">Lorem ipsum dolor sit amet, consectetur adipiscing elit, sed do eiusmod tempor incididunt ut labore et dolore magna aliqua. Quis ipsum suspendisse ultrices gravida. Risus commodo viverra maecenas accumsan lacus vel facilisis.</p>
<div class="field" style="left:177px;top:3952px;width:383px;height:54px">First Name</div>
<div class="field" style="left:578px;top:3952px;width:385px;height:54px">Last Name</div>
<div class="field" style="left:177px;top:4018px;width:383px;height:54px">Email</div>
<div class="field" style="left:578px;top:4018px;width:385px;height:54px">Telephone Number</div>
<div class="field" style="left:177px;top:4087px;width:786px;height:103px;align-items:flex-start;padding-top:20px">How Can We Help?</div>
<div class="abs" style="left:184px;top:4218px;font-size:12.5px;color:#222;display:flex;gap:8px;align-items:center"><span style="color:var(--blue)">✔</span>By submitting this form, I accept Paperlynx's privacy policy .</div>
<div class="abs" style="left:502px;top:4290px;width:194px;height:52px;border-radius:30px;background:var(--blue);color:#fff;font-family:'Barlow Semi Condensed',sans-serif;font-weight:700;font-size:18px;display:flex;align-items:center;justify-content:center">BOOK A DEMO</div>

<footer class="site-footer">
  <div class="abs" style="left:0;top:85px;width:1200px;text-align:center;font-family:'Barlow Semi Condensed',sans-serif;font-weight:700;font-size:56px;color:var(--blue-2);letter-spacing:1px">PAPERLYNX</div>
  <div class="abs" style="left:0;top:152px;width:1200px;text-align:center;font-size:15px;letter-spacing:4px;color:#2a6d8c">CREATING SIGNABLE DOCUMENTS</div>

  <h3 class="foot-h" style="left:111px">Help links</h3>
  <ul class="foot-list" style="left:111px;top:272px"><li>Terms &amp; Condtions</li><li>Privacy Policy</li><li>About Us</li><li>Support</li></ul>

  <h3 class="foot-h" style="left:276px">Subscribe to our newsletter</h3>
  <p class="abs" style="left:278px;top:274px;width:300px;font-size:14px;line-height:24px">Lorem ipsum dolor sit amet, consectetur adipiscing elit, sed do</p>
  <div class="abs" style="left:276px;top:338px;width:274px;height:44px;border:1px solid #777;border-radius:24px;font-size:13px;color:#bbb;padding:0 20px;display:flex;align-items:center">Enter Your Email</div>
  <svg class="abs" style="left:510px;top:346px" width="30" height="30"><circle cx="15" cy="15" r="14" fill="#1c9ad6"/><path d="M8 15 L22 9 L17 22 L15 16 Z" fill="#fff"/></svg>

  <h3 class="foot-h" style="left:653px">Contact us</h3>
  <div class="abs" style="left:655px;top:276px;font-size:14.5px;line-height:24px">
    <div style="display:flex;gap:14px"><span>●</span><span>Lindevej 214,<br>2640 Hedehusene</span></div>
    <div style="display:flex;gap:14px;margin-top:10px"><span>✉</span><span>contact@paperlynx.example</span></div>
    <div style="display:flex;gap:14px;margin-top:10px"><span>✆</span><span>+45 30 00 19 47</span></div>
  </div>

  <h3 class="foot-h" style="left:896px">About us</h3>
  <p class="abs" style="left:892px;top:274px;width:210px;font-size:12.5px;line-height:23px">We would love to link and share thoughts and ideas. Follow us and stay updated on the latest news.</p>

  <div class="abs" style="left:0;top:508px;width:1200px;text-align:center;font-size:14px">©Copyrights 2024 Paperlynx. &nbsp;| &nbsp; All Rights Reserved</div>
</footer>

</body>
</html>
```